Website for a company offering full serivce charging solutions for electric cars

The company "tanu-werk" (english: "tanu-works") offering all-in-one-solutions for charging infrastructure for electric mobility.

There are four products:
1- Wallboxes for single-family homes
2- Solutions for property devloper/-management for property parking space
3- All-in-one-charging solution for municipalities/communities
4- Solutions for tourism/hotels/holiday appartments

The Website structure:
1. Main Page
2.1. Product Page Single Homes
2.2. Product Page Property Management / Parking
2.3. Product Page Municipality
2.4. Product Page Tourism
3. Contact Form / Request for information
4. Imprint / Legal

The Website should be built on Wordpress with a powerful possibility to simply add/modify specific landing pages.

We would like you to implement the website later and also maintain it if possible, but we would be able to do minor modifications by ourselfs (for A/B-Testing)

The website should be clear and simple, easy to understand.
Target group is mainly B2C without deeper knowledge of that topic.

It should suggest, that we will provide a very simple way to get the charging infrastructure done.

We need a contact form, maybe we will use Hubspot later.

Attached you will find a draft of the main page and a landing page (for 2.2) - it is just the content, please ignore the design. We would love to let you create a suitable design.
Also you will find some drafts a bit different for the same story.

I added also a few stock photos, but they don't need to be used! If you have better ideas, you are welcome!

Industry/Entity Type

Charging/Electric mobility

Number of Pages Required

2 page

Font styles to use
Sans Serif

Requirements
Must have
• Based on Wordpress, and the designer should be able to implement it on Wordpress on a later step

```html
<!DOCTYPE html>
<html lang="de">
<head>
<meta charset="utf-8">
<title>tanu-werk – Ihr Partner für Ladelösungen</title>
<link href="https://fonts.googleapis.com/css2?family=Exo:wght@500;600;700&family=Poppins:wght@300;400;500;600&display=swap" rel="stylesheet">
<style>
:root{
  --pink:#e1179b;
  --purple:#7a5cc6;
  --grad:linear-gradient(90deg,#e1179b,#8a4fd0);
  --ink:#1b1b1f;
  --text:#5a5a60;
  --muted:#f4f4f4;
  --navy:#0c1127;
  --white:#fff;
}
*{margin:0;padding:0;box-sizing:border-box}
html,body{width:1200px;height:3549px;overflow:hidden}
body{font-family:'Poppins',sans-serif;color:var(--text);background:var(--white);position:relative}
.heading{font-family:'Exo',sans-serif}

/* hero */
.hero{position:absolute;left:0;top:0;width:1200px;height:597px}
.hero-photo{position:absolute;inset:0;background:
  radial-gradient(circle at 80% 45%,#3f5fc9 0,#1d2a6a 14%,transparent 32%),
  radial-gradient(circle at 45% 25%,#5a5170 0,transparent 30%),
  linear-gradient(100deg,#17151f 0%,#2a2534 45%,#34303e 70%,#1c1a22 100%)}
.brand{position:absolute;display:flex;align-items:center;gap:10px;font-family:'Exo',sans-serif;font-weight:600}
.brand .dot{width:22px;height:22px;border-radius:50%;background:var(--pink)}
.hero .brand{left:160px;top:36px;color:var(--white);font-size:28px}
.nav{position:absolute;left:409px;top:34px;display:flex;gap:32px;font-family:'Exo',sans-serif;font-size:12px;font-weight:600;color:var(--white)}
.nav-cta{position:absolute;left:931px;top:25px;width:107px;height:36px;border-radius:18px;background:var(--grad);color:var(--white);font-family:'Exo',sans-serif;font-size:12px;font-weight:700;display:flex;align-items:center;justify-content:center}
.hero-title{position:absolute;left:163px;top:182px;font-size:58px;line-height:66px;font-weight:600;color:var(--white)}
.hero-sub{position:absolute;left:163px;top:326px;width:340px;font-size:19px;line-height:26px;font-weight:300;color:var(--white)}
.hero-cta{position:absolute;left:163px;top:427px;width:243px;height:43px;border-radius:22px;background:var(--grad);color:var(--white);font-family:'Exo',sans-serif;font-size:13px;font-weight:700;display:flex;align-items:center;justify-content:center}

/* intro */
.intro-ring{position:absolute;left:179px;top:689px;width:414px;height:414px;border-radius:50%;background:var(--purple)}
.intro-photo{position:absolute;left:198px;top:705px;width:375px;height:450px;background:linear-gradient(180deg,#e9a23a 0%,#c46b2a 40%,#5a4a3c 75%,#d8d8d8 100%);box-shadow:0 10px 24px rgba(0,0,0,.25)}
.intro{position:absolute;left:639px;top:730px;width:390px}
.intro h2{font-size:31px;font-weight:600;color:var(--ink);margin-bottom:12px}
.intro .lead{font-size:13px;font-weight:600;line-height:22px;color:var(--ink);margin-bottom:12px}
.intro p{font-size:12.5px;line-height:21.5px;margin-bottom:13px}
.pill{display:inline-flex;align-items:center;gap:14px;height:41px;padding:0 26px 0 4px;border:1.5px solid #333;border-radius:21px;font-size:14px;color:var(--ink)}
.pill .dot{width:33px;height:33px;border-radius:50%;background:var(--grad)}

.section-title{position:absolute;left:0;top:1242px;width:1200px;text-align:center;font-size:31px;line-height:44px;font-weight:500;color:var(--ink)}

/* offers */
.offer{position:absolute;left:0;width:1200px;height:600px}
.offer .panel{position:absolute;top:0;width:600px;height:100%;background:var(--muted)}
.offer .photo{position:absolute;top:0;width:600px;height:100%}
.offer .copy{position:absolute;width:380px}
.offer h3{font-family:'Exo',sans-serif;font-size:21px;font-weight:500;color:var(--purple);margin-bottom:14px}
.offer ul{list-style:none;margin-bottom:22px}
.offer li{position:relative;padding-left:19px;font-size:12.5px;line-height:20px;margin-bottom:7px}
.offer li::before{content:"";position:absolute;left:0;top:6px;width:7px;height:7px;border:1.5px solid var(--pink);border-radius:50%}
.offer li.sub{padding-left:37px}
.offer li.sub::before{left:20px;top:7px;width:6px;height:6px;border:0;background:var(--pink)}

/* contact bar */
.contact{position:absolute;left:0;top:3153px;width:1200px;height:135px;background:var(--navy)}
.contact-item{position:absolute;top:52px;display:flex;gap:14px;color:var(--white);font-size:14px;line-height:22px}
.contact-item .icon{width:46px;height:38px;background:var(--grad);clip-path:polygon(12% 0,100% 0,88% 100%,0 100%);display:flex;align-items:center;justify-content:center;margin-top:-4px}
.contact-item strong{font-weight:400;font-size:15px;display:block}

/* footer */
.footer .brand{left:484px;top:3325px;color:var(--ink);font-size:26px}
.footer-links{position:absolute;left:0;top:3392px;width:1200px;display:flex;justify-content:center;gap:54px;font-size:13px;color:var(--ink)}
.copyright{position:absolute;left:0;top:3433px;width:1200px;text-align:center;font-size:12.5px;color:var(--ink)}
.social{position:absolute;left:527px;top:3472px;display:flex;gap:18px}
.social span{width:36px;height:36px;border-radius:50%;background:var(--grad)}
.bottom-line{position:absolute;left:0;top:3545px;width:1200px;height:4px;background:var(--grad)}
</style>
</head>
<body>

<header class="hero">
  <div class="hero-photo" role="img" aria-label="Ladestecker steckt in einer Ladesäule, Lichter im Hintergrund"></div>
  <div class="brand"><span class="dot"></span>tanu-werk.de</div>
  <nav class="nav"><span>einfach mehr als laden</span><span>Lösungen</span><span>Unternehmen</span><span>Services</span><span>Karriere</span></nav>
  <a class="nav-cta">Kontakt</a>
  <h1 class="hero-title heading">tanu-werk ist<br>Ihr Partner</h1>
  <p class="hero-sub">wenn das Laden nicht nur einfach, sondern die Umsetzung auch aus einer Hand kommen soll</p>
  <a class="hero-cta">Kontaktieren Sie uns heute</a>
</header>

<div class="intro-ring"></div>
<div class="intro-photo" role="img" aria-label="Frau mit Smartphone neben einem ladenden Elektroauto bei Sonnenuntergang"></div>
<section class="intro">
  <h2 class="heading">Tanu-werk Ist Ihr Partner</h2>
  <p class="lead">Wenn das Laden nicht nur einfach, sondern die Umsetzung auch aus einer Hand kommen soll</p>
  <p>Wir bieten Lösungen sowohl für Privatkunden, Geschäftskunden als auch Kommunen an, die schnell, fair und ohne Eigenleistung zu einer smarten Ladelösung für E-Fahrzeuge kommen möchten.</p>
  <p>Von der Beratung, über die Installation, Inbetriebnahme bis zur Abrechnung und Wartung bekommen Sie bei tanu-werk alles aus einer Hand. Auf Wunsch vermieten wir auch die Ladetechnik und übernehmen im gewerblichen Bereich die direkte Abrechnung mit dem Nutzer. Für Kommunen bieten wir den kostenfreien Full-Service an und beteiligen die Gemeinden an der Nutzung der Infrastruktur.</p>
  <a class="pill"><span class="dot"></span>Weiterlesen</a>
</section>

<h2 class="section-title heading">Fragen Sie Uns Nach Der Auf Ihre Individuellen<br>Bedürfnisse Zugeschnittenen Lösung</h2>

<section class="offer" style="top:1357px">
  <div class="panel" style="left:0"></div>
  <div class="photo" style="left:600px;background:linear-gradient(180deg,#b9d3ea 0%,#ece8df 35%,#d9d2c4 70%,#b8a58f 100%)" role="img" aria-label="Modernes weißes Wohnhaus mit gepflastertem Vorplatz"></div>
  <div class="copy" style="left:163px;top:138px">
    <h3>Als Privatkunde</h3>
    <ul>
      <li>Bestandsanalyse mit umfangreicher Beratung über die Möglichkeiten der Umsetzung</li>
      <li>Prüfung und Übernahme der Anmeldung verfügbarer Fördermöglichkeiten</li>
      <li>Auswahl an smarten Wallbox Lösungen, passend für Ihr Fahrzeug und Ihre Bedürfnisse</li>
      <li>Installation inkl. aller notwendigen Materialien und Tätigkeiten (Durchbrüche, Erdarbeiten, etc.)</li>
      <li>Inbetriebnahme und Einweisung in die Ladetechnik</li>
    </ul>
    <a class="pill"><span class="dot"></span>Alle Ansehen</a>
  </div>
</section>

<section class="offer" style="top:1957px">
  <div class="photo" style="left:0;background:linear-gradient(135deg,#d8c2a4 0%,#c9a983 45%,#e6ddd2 100%)" role="img" aria-label="Team arbeitet an einem Holztisch mit Laptops, Ansicht von oben"></div>
  <div class="panel" style="left:600px;background:var(--white)"></div>
  <div class="copy" style="left:668px;top:116px;width:370px">
    <h3>Als Geschäftskunde</h3>
    <ul>
      <li>Durchführung einer individuellen Bedarfsanalyse inkl. Ermittlung der Anforderungen für:</li>
      <li class="sub">Haus- und Immobilienverwaltungen</li>
      <li class="sub">Dienstleistungs- und Handelsunternehmen</li>
      <li class="sub">Hotel und Beherbergungsbetriebe</li>
      <li class="sub">Parkraum- und Parkhausbetreiber</li>
      <li class="sub">Tourismus, Sport- und Freizeiteinrichtungen</li>
      <li>Planung und Projektierung des Installationsaufwands inkl. Materialverbrauch</li>
      <li>Leasing oder Kauf der Hardware</li>
    </ul>
    <a class="pill"><span class="dot"></span>Alle Ansehen</a>
  </div>
</section>

<section class="offer" style="top:2557px;height:596px">
  <div class="panel" style="left:0"></div>
  <div class="photo" style="left:600px;background:linear-gradient(180deg,#2f6fd0 0%,#5f95de 30%,#cdbb98 55%,#a88e6c 85%,#9b9b9b 100%)" role="img" aria-label="Historisches Thermalbad-Gebäude vor blauem Himmel"></div>
  <div class="copy" style="left:163px;top:136px">
    <h3>Als Kommune</h3>
    <ul>
      <li>Konzeptionierung möglicher Ladeinfrastrukturen innerhalb Ihrer Gemeinde</li>
      <li>Planung und Projektsteuerung inkl. sämtlicher behördlicher Genehmigungsverfahren und Beantragung von Fördermitteln</li>
      <li>Fachgerechte Installation und Inbetriebnahme</li>
      <li>Regelmäßige Wartung gemäß Vorschrif</li>
      <li>Reparatur und Kundenservice</li>
      <li>Direkte Abrechnung mit dem Nutzer</li>
    </ul>
    <a class="pill"><span class="dot"></span>Alle Ansehen</a>
  </div>
</section>

<section class="contact">
  <div class="contact-item" style="left:160px">
    <span class="icon"><svg width="16" height="16" viewBox="0 0 24 24"><path fill="#fff" d="M6.6 10.8a15 15 0 0 0 6.6 6.6l2.2-2.2c.3-.3.7-.4 1-.2 1.1.4 2.3.6 3.6.6.6 0 1 .4 1 1V20c0 .6-.4 1-1 1A17 17 0 0 1 3 4c0-.6.4-1 1-1h3.5c.6 0 1 .4 1 1 0 1.3.2 2.5.6 3.6.1.3 0 .7-.2 1z"/></svg></span>
    <div><strong>Anruf</strong>123 456 7890 (Zollfrei)</div>
  </div>
  <div class="contact-item" style="left:435px">
    <span class="icon"><svg width="16" height="14" viewBox="0 0 24 20"><path fill="#fff" d="M2 2h20v16H2z" opacity=".0"/><path fill="#fff" d="M2 2h20v2l-10 6L2 4zm0 4l10 6 10-6v12H2z"/></svg></span>
    <div><strong>Email</strong>info@tanu-werk.de.com</div>
  </div>
  <div class="contact-item" style="left:708px">
    <span class="icon"><svg width="16" height="16" viewBox="0 0 24 24"><path fill="#fff" d="M6.6 10.8a15 15 0 0 0 6.6 6.6l2.2-2.2c.3-.3.7-.4 1-.2 1.1.4 2.3.6 3.6.6.6 0 1 .4 1 1V20c0 .6-.4 1-1 1A17 17 0 0 1 3 4c0-.6.4-1 1-1h3.5c.6 0 1 .4 1 1 0 1.3.2 2.5.6 3.6.1.3 0 .7-.2 1z"/></svg></span>
    <div><strong>Ein Kleid</strong>12 Gebäude, Straße, Stadt, Bundesland</div>
  </div>
</section>

<footer class="footer">
  <div class="brand"><span class="dot"></span>tanu-werk.de</div>
  <nav class="footer-links"><span>AGB</span><span>Datenschutzerklärung</span><span>Impressum</span><span>Kontakt</span><span>Karriere</span><span>FAQs</span></nav>
  <p class="copyright">Urheberrecht © 2022 tanu-werk.de. Alle Rechte vorbehalten.</p>
  <div class="social"><span aria-label="Video-Kanal"></span><span aria-label="Soziales Netzwerk"></span><span aria-label="Foto-Netzwerk"></span></div>
  <div class="bottom-line"></div>
</footer>

</body>
</html>
```